Coral Bay Pools New website

I currently operate a swimming pool service and repair business and looking for a re design for my website as it has been over 5 years since it was designed. current site is coralbaypoolslv.com

```html
<!DOCTYPE html>
<html lang="en">
<head>
<meta charset="utf-8">
<title>Coral Bay Pools</title>
<link rel="stylesheet" href="https://fonts.googleapis.com/css2?family=Playfair+Display:ital,wght@0,700;0,900;1,700&family=Montserrat:wght@400;500;600;700&family=Poppins:wght@400;500;600&family=Parisienne&display=swap">
<style>
:root{
  --navy:#0f4f95;
  --blue:#1b62a8;
  --sky:#27b6ea;
  --aqua:#5fc9ef;
  --orange:#f7a933;
  --orange-dark:#e8921a;
  --ink:#222;
  --white:#fff;
  --footer:#0d4b8e;
}
*{margin:0;padding:0;box-sizing:border-box}
html,body{width:1200px;height:5286px;overflow:hidden}
body{position:relative;font-family:"Montserrat",sans-serif;color:var(--ink);background:var(--white)}
.abs{position:absolute}
.serif{font-family:"Playfair Display",serif}
.btn{position:absolute;display:flex;align-items:center;justify-content:center;gap:12px;border-radius:40px;color:var(--white);font-family:"Poppins",sans-serif;font-weight:500;letter-spacing:.5px;text-transform:uppercase}
.btn svg{width:20px;height:20px}
.btn-orange{background:var(--orange)}
.btn-navy{background:var(--navy)}

/* header */
.site-header{position:absolute;left:0;top:37px;width:1200px;height:70px;background:var(--navy);z-index:5}
.brand{position:absolute;left:76px;top:0;height:70px;display:flex;align-items:center;gap:12px;font-family:"Montserrat",sans-serif;font-weight:700;font-size:24px;color:var(--white)}
.brand .dot{width:34px;height:34px;border-radius:50%;background:var(--orange)}
.main-nav{position:absolute;left:452px;top:0;height:70px;display:flex;align-items:center;gap:0;font-size:12.5px;font-weight:500;color:var(--white)}
.main-nav span{margin-right:46px}
.main-nav .cta{margin:0;background:var(--orange);border-radius:20px;padding:10px 14px}

/* hero */
.hero{left:0;top:0;width:1200px;height:997px;background:linear-gradient(100deg,#5a87b5 0%,#7fa7cb 28%,#9fc3d9 48%,#4cb6d9 62%,#1f9bcf 80%,#55c4e6 100%)}
.hero-shade{left:0;top:0;width:620px;height:997px;background:linear-gradient(90deg,rgba(22,84,150,.75),rgba(22,84,150,0))}
.welcome{left:58px;top:290px;font-family:"Parisienne",cursive;font-size:64px;color:var(--white)}
.hero-title{left:58px;top:392px;font-size:92px;line-height:108px;font-weight:900;color:var(--white);letter-spacing:1px}
.hero-sub{left:66px;top:648px;font-family:"Montserrat",sans-serif;font-size:40px;line-height:50px;font-weight:600;color:var(--white)}
.hero-btn{left:68px;top:830px;width:254px;height:67px;font-size:22px}

/* features */
.features{left:0;top:997px;width:1200px;height:242px;background:linear-gradient(180deg,#29b7ec 0%,#1a8fd1 55%,#1565b0 100%)}
.feature{position:absolute;top:42px;width:180px;text-align:center;color:var(--white);font-family:"Poppins",sans-serif;font-size:15px;line-height:19px}
.feature .ring{width:96px;height:96px;margin:0 auto 14px;border-radius:50%;background:var(--white);border:3px solid #d7eefc;display:flex;align-items:center;justify-content:center}
.feature .ring svg{width:52px;height:52px}

/* about */
.about-ring{left:71px;top:1363px;width:440px;height:440px;border-radius:50%;border:3px solid var(--navy)}
.about-photo{left:91px;top:1383px;width:400px;height:400px;border-radius:50%;background:radial-gradient(circle at 40% 60%,#2fb4e6,#1480bf 60%,#6c9b5a 100%)}
.about-photo-small{left:341px;top:1678px;width:192px;height:192px;border-radius:50%;border:5px solid var(--white);background:linear-gradient(160deg,#7ea860,#3aa7d5 60%,#1d7fbf)}
.section-title{font-family:"Playfair Display",serif;font-weight:900;color:var(--navy);text-transform:uppercase}
.about-title{left:597px;top:1380px;font-size:52px}
.eyebrow{font-family:"Montserrat",sans-serif;color:var(--orange);font-size:20px;font-weight:500;text-transform:uppercase;display:flex;align-items:center;gap:10px}
.eyebrow i{display:block;height:2px;background:var(--orange)}
.about-eyebrow{left:595px;top:1438px}
.about-lead{left:595px;top:1490px;width:500px;font-size:27px;line-height:32px;color:#111;font-weight:500}
.about-copy{left:595px;top:1571px;width:500px;font-size:13px;line-height:24px;color:#222}
.about-btn{left:589px;top:1780px;width:201px;height:51px;font-size:17px}

/* services */
.services-band{left:0;top:1990px;width:1200px;height:438px;background:linear-gradient(180deg,#2a75b8,#1c5fa4)}
.services-title{left:0;top:2052px;width:1200px;text-align:center;color:var(--white);font-size:50px}
.services-eyebrow{left:0;top:2118px;width:1200px;justify-content:center}
.services-note{left:0;top:2184px;width:1200px;text-align:center;color:var(--white);font-size:13px}
.service{position:absolute;top:2290px;width:300px;text-align:center}
.service .disc{width:254px;height:254px;margin:0 auto;border-radius:50%;border:8px solid var(--white);border-top-color:var(--orange);border-left-color:var(--orange)}
.service h3{margin-top:36px;font-size:31px;line-height:37px;font-weight:600;color:var(--navy);text-transform:uppercase}
.service p{margin:18px auto 0;width:260px;font-size:13px;line-height:24px;color:#222}
.service .btn{position:relative;margin:18px auto 0;width:150px;height:38px;font-size:12px;background:var(--orange);opacity:.9}

/* pool band */
.pool-band{left:0;top:2790px;width:1200px;height:533px;background:linear-gradient(180deg,#ffffff 0%,#e3f2f7 22%,#6ec3de 45%,#1b8db8 62%,#4da3b8 80%,#ffffff 100%)}

/* why */
.why-title{left:0;top:3324px;width:1200px;text-align:center;font-size:50px}
.why-text{left:0;top:3440px;width:1200px;text-align:center;font-size:17px;line-height:29px;font-weight:600;color:#111}
.why-lead{left:0;top:3500px;width:1200px;text-align:center;font-family:"Playfair Display",serif;font-style:italic;font-weight:700;font-size:42px;line-height:52px;color:var(--navy)}
.why-cta{left:0;top:3612px;width:1200px;text-align:center;font-size:28px;color:var(--orange);letter-spacing:1px}
.why-btn{left:500px;top:3678px;width:200px;height:55px;font-size:19px}

/* blog */
.blog-title{left:0;top:3880px;width:1200px;text-align:center;font-size:50px}
.blog-eyebrow{left:0;top:3944px;width:1200px;justify-content:center}
.blog-arrow{width:34px;height:34px;border-radius:50%;display:flex;align-items:center;justify-content:center}
.post{position:absolute;top:4034px;width:300px;height:400px}
.post .thumb{position:absolute;left:0;top:0;width:267px;height:273px;border-radius:22px}
.post .body{position:absolute;left:70px;top:200px;width:210px;height:190px;background:var(--white);border-radius:22px 0 0 0;padding:20px 0 0 14px}
.post .date{font-size:12px;color:#333;display:flex;align-items:center;gap:10px}
.post .date i{display:block;width:16px;height:16px;background:#f6d9a8;border-radius:3px}
.post h4{margin-top:12px;font-size:17px;line-height:21px;font-weight:500;color:var(--blue)}
.post p{margin-top:14px;font-size:13px;line-height:21px;color:#333}
.post .btn{position:relative;margin-top:12px;width:100px;height:30px;font-size:12px;font-weight:600}

/* contact */
.contact-photo{left:0;top:4451px;width:1200px;height:517px;background:linear-gradient(180deg,#f3f7f6 0%,#cfe7ee 40%,#34a8d6 72%,#1a83c1 100%)}
.contact-fade{left:0;top:4451px;width:1200px;height:300px;background:linear-gradient(90deg,rgba(255,255,255,0) 0%,rgba(255,255,255,.85) 55%,rgba(255,255,255,.6) 100%)}
.contact-title{left:642px;top:4510px;font-family:"Montserrat",sans-serif;font-weight:700;font-size:46px;color:var(--navy)}
.contact-eyebrow{left:644px;top:4568px}
.field{position:absolute;background:var(--white);border:1px solid #d5d5d5;font-size:13px;color:#444;padding:14px 0 0 18px}
.submit{left:644px;top:4865px;width:162px;height:53px;font-size:19px}

/* footer */
.site-footer{left:0;top:4968px;width:1200px;height:318px;background:var(--footer);color:var(--white)}
.foot-brand{position:absolute;left:80px;top:46px;display:flex;align-items:center;gap:12px;font-weight:700;font-size:22px}
.foot-brand .dot{width:30px;height:30px;border-radius:50%;background:var(--orange)}
.foot-item{position:absolute;top:60px;display:flex;align-items:center;gap:14px;font-family:"Poppins",sans-serif;font-size:14px;line-height:19px}
.foot-item .badge{width:44px;height:44px;display:flex;align-items:center;justify-content:center}
.foot-rule{position:absolute;left:64px;width:1070px;height:1px;background:rgba(255,255,255,.55)}
.foot-nav{position:absolute;left:0;top:202px;width:1200px;text-align:center;font-size:13px;font-weight:500}
.foot-nav span{margin:0 30px}
.copyright{position:absolute;left:60px;top:274px;font-size:12px}
.social{position:absolute;top:268px;width:26px;height:26px;background:var(--white);border-radius:3px}
</style>
</head>
<body>

<!-- hero -->
<div class="abs hero" role="img" aria-label="Photo of a resort swimming pool with blue tiles, a fountain spray and a white pavilion"></div>
<div class="abs hero-shade"></div>

<header class="site-header">
  <div class="brand"><span class="dot"></span>Coral Bay Pools</div>
  <nav class="main-nav">
    <span>HOME</span><span>ABOUT US</span><span>OUR SERVICES</span><span>BLOG</span><span>FREE ESTIMATE</span><span class="cta">CONTACT US</span>
  </nav>
</header>

<div class="abs welcome">Welcome To</div>
<h1 class="abs hero-title serif">CORAL BAY<br>POOLS</h1>
<p class="abs hero-sub">NEVADA’S TOP RATED<br>LOCAL® POOL<br>CLEANING</p>
<div class="btn btn-orange hero-btn">Free Estimate
  <svg viewBox="0 0 20 20" fill="none" stroke="#fff" stroke-width="1.8"><path d="M3 10h12M11 5l5 5-5 5"/></svg>
</div>

<!-- features -->
<section class="abs features">
  <div class="feature" style="left:97px"><div class="ring"><svg viewBox="0 0 52 52" fill="none" stroke="#1b62a8" stroke-width="2.2"><rect x="12" y="18" width="28" height="20" rx="4"/><path d="M18 18v-8M26 18v-8M34 18v-8M16 38v5M36 38v5"/></svg></div>Vacuum and<br>brush your pool</div>
  <div class="feature" style="left:300px"><div class="ring"><svg viewBox="0 0 52 52" fill="none" stroke="#1b62a8" stroke-width="2.2"><rect x="12" y="10" width="28" height="34" rx="2"/><path d="M26 18v10M21 23h10M18 36l16-6"/></svg></div>Thoroughly<br>clean the tiles</div>
  <div class="feature" style="left:482px"><div class="ring"><svg viewBox="0 0 52 52" fill="none" stroke="#1b62a8" stroke-width="2.2"><rect x="14" y="12" width="24" height="32" rx="3"/><circle cx="26" cy="30" r="6"/><path d="M20 12V8h12v4"/></svg></div>Balance the<br>chemicals</div>
  <div class="feature" style="left:671px"><div class="ring"><svg viewBox="0 0 52 52" fill="none" stroke="#1b62a8" stroke-width="2.2"><path d="M12 22h28l-4 20H16z"/><path d="M18 22l6-10M34 22l-6-10M20 28v10M26 28v10M32 28v10"/></svg></div>Remove and clean<br>all the baskets</div>
  <div class="feature" style="left:872px"><div class="ring"><svg viewBox="0 0 52 52" fill="none" stroke="#1b62a8" stroke-width="2.2"><rect x="10" y="16" width="22" height="22" rx="6"/><circle cx="21" cy="27" r="5"/><path d="M32 22h8v10h-8"/></svg></div>Clean the filter<br>when necessary</div>
</section>

<!-- about -->
<div class="abs about-ring"></div>
<div class="abs about-photo" role="img" aria-label="Photo of a clear blue pool with a metal ladder and loungers"></div>
<div class="abs about-photo-small" role="img" aria-label="Photo of a pool cleaning net skimming the water"></div>
<h2 class="abs section-title about-title">About Us</h2>
<div class="abs eyebrow about-eyebrow">Coral Bay Pools <i style="width:50px"></i></div>
<p class="abs about-lead">We are a full service pool company servicing the Las Vegas Valley</p>
<p class="abs about-copy">When you need professional pool cleaning services in Nevada, you can count on the professionals at Coral Bay Pools to provide you with superior and prompt solutions. Whether you need assistance with a residential or commercial pool, we’ll vacuum, brush, and thoroughly clean your pool so it’s swim-ready. We’ll also clean your pool filters and inform you of any issues that arise. Our staff is certified by the Desert Valley Health Authority to ensure proper chemical levels and equipment are safe.</p>
<div class="btn btn-navy about-btn">Learn More
  <svg viewBox="0 0 20 20" fill="none" stroke="#fff" stroke-width="1.8"><path d="M3 10h12M11 5l5 5-5 5"/></svg>
</div>

<!-- services -->
<div class="abs services-band" role="img" aria-label="Faded photo of a pool with palm trees behind a blue overlay"></div>
<h2 class="abs section-title services-title">Our Services</h2>
<div class="abs eyebrow services-eyebrow"><i style="width:80px"></i>What We Do<i style="width:80px"></i></div>
<p class="abs services-note">We’re certified by the Desert Valley Health Authority to maintain proper chemical levels and operate equipment in a safe manner.</p>

<div class="service" style="left:88px">
  <div class="disc" role="img" aria-label="Photo of a blue pool skimmer net in the water" style="background:radial-gradient(circle,#3fc0ef,#1590cf)"></div>
  <h3>Pool Services</h3>
  <p>When you invested in your pool, you knew it was a long-term investment in both money and time</p>
  <div class="btn">Learn More</div>
</div>
<div class="service" style="left:449px">
  <div class="disc" role="img" aria-label="Photo of a commercial pool with a ladder" style="background:linear-gradient(180deg,#8aa87b,#3aaedc 55%,#1b86c6)"></div>
  <h3>Commercial<br>Pool Services</h3>
  <p>As a commercial property owner or manager, doing your job well requires</p>
  <div class="btn">Learn More</div>
</div>
<div class="service" style="left:810px">
  <div class="disc" role="img" aria-label="Photo of a family relaxing on a pool float" style="background:linear-gradient(180deg,#cfeefc,#f2c98a 60%,#f3e178)"></div>
  <h3>Residential<br>Pool Services</h3>
  <p>Here in Southern Nevada, you know it can get really, really hot. That’s why you</p>
  <div class="btn">Learn More</div>
</div>

<div class="abs pool-band" role="img" aria-label="Wide photo of a curved resort pool with ladders and palm trees"></div>

<!-- why -->
<h2 class="abs section-title why-title">Why Choose Us?</h2>
<p class="abs why-text">Our full-service pool company proudly serves the entire Las Vegas valley, and we’re certified by the<br>Desert Valley Health Authority to maintain the highest level of pool safety</p>
<p class="abs why-lead">If you need repairs, maintenance, scheduled<br>cleanings, or any other pool services,</p>
<p class="abs why-cta">CONTACT US ONLINE OR BY PHONE TODAY.</p>
<div class="btn btn-orange why-btn">Contact Us
  <svg viewBox="0 0 20 20" fill="none" stroke="#fff" stroke-width="1.8"><path d="M3 10h12M11 5l5 5-5 5"/></svg>
</div>

<!-- blog -->
<h2 class="abs section-title blog-title">Latest Blog</h2>
<div class="abs eyebrow blog-eyebrow"><i style="width:50px"></i>News&amp; Updates<i style="width:50px"></i></div>
<div class="abs blog-arrow" style="left:47px;top:4161px;background:#e2e2e2"><svg width="12" height="12" viewBox="0 0 12 12" fill="none" stroke="#555" stroke-width="2"><path d="M8 2L4 6l4 4"/></svg></div>
<div class="abs blog-arrow" style="left:1115px;top:4161px;background:var(--orange)"><svg width="12" height="12" viewBox="0 0 12 12" fill="none" stroke="#fff" stroke-width="2"><path d="M4 2l4 4-4 4"/></svg></div>

<article class="post" style="left:117px">
  <div class="thumb" role="img" aria-label="Photo of a resort pool with thatched cabanas" style="background:linear-gradient(180deg,#a88a5e,#d9c7a8 40%,#49b3dd 70%,#1e86c4)"></div>
  <div class="body"><div class="date"><i></i>18 March 2025</div><h4>Lorem ipsum dolor sit<br>ame etconsectetur</h4><p>Lorem ipsum dolor sit<br>amet, consectetur adip</p><div class="btn btn-navy">Read More</div></div>
</article>
<article class="post" style="left:461px">
  <div class="thumb" role="img" aria-label="Photo of a pool surrounded by palm trees" style="background:linear-gradient(180deg,#e9f3f5,#6f9d59 35%,#2fb0d8 70%,#1c80bf)"></div>
  <div class="body"><div class="date"><i></i>18 March 2025</div><h4>Lorem ipsum dolor sit<br>ame etconsectetur</h4><p>Lorem ipsum dolor sit<br>amet, consectetur adip</p><div class="btn btn-navy">Read More</div></div>
</article>
<article class="post" style="left:800px">
  <div class="thumb" role="img" aria-label="Photo of a pool ladder over blue tiles" style="background:linear-gradient(180deg,#7ca46a,#2c8fd0 35%,#1562b4 70%,#3a9ad6)"></div>
  <div class="body"><div class="date"><i></i>18 March 2025</div><h4>Lorem ipsum dolor sit<br>ame etconsectetur</h4><p>Lorem ipsum dolor sit<br>amet, consectetur adip</p><div class="btn btn-navy">Read More</div></div>
</article>

<!-- contact -->
<div class="abs contact-photo" role="img" aria-label="Photo of a pool with a ladder and loungers under trees"></div>
<div class="abs contact-fade"></div>
<h2 class="abs contact-title">CONTACT US</h2>
<div class="abs eyebrow contact-eyebrow" style="font-size:18px;color:var(--blue)">Coral Bay Pools <i style="width:140px"></i></div>
<div class="field" style="left:642px;top:4636px;width:240px;height:40px;padding-top:12px">Your Name</div>
<div class="field" style="left:890px;top:4636px;width:236px;height:40px;padding-top:10px">Phone Number</div>
<div class="field" style="left:642px;top:4687px;width:484px;height:41px;padding-top:12px">Email Address</div>
<div class="field" style="left:642px;top:4738px;width:484px;height:78px">Message</div>
<div class="btn btn-orange submit">Submit
  <svg viewBox="0 0 20 20" fill="none" stroke="#fff" stroke-width="1.8"><path d="M3 10h12M11 5l5 5-5 5"/></svg>
</div>

<!-- footer -->
<footer class="abs site-footer">
  <div class="foot-brand"><span class="dot"></span>Coral Bay Pools</div>
  <div class="foot-item" style="left:290px"><div class="badge"><svg viewBox="0 0 44 44" width="44" height="44" fill="none" stroke="#fff" stroke-width="2"><rect x="10" y="10" width="24" height="24" transform="rotate(45 22 22)"/><path d="M17 16c0 7 4 11 11 12l2-3-3-2-2 1c-2-1-3-2-4-4l1-2-2-3z" fill="#fff" stroke="none"/></svg></div><div>CALL US<br>(702) 555-0148</div></div>
  <div class="foot-item" style="left:510px"><div class="badge"><svg viewBox="0 0 44 44" width="44" height="44" fill="none" stroke="#fff" stroke-width="2"><rect x="10" y="10" width="24" height="24" transform="rotate(45 22 22)"/><rect x="15" y="17" width="14" height="10"/><path d="M15 17l7 6 7-6"/></svg></div><div>EMAIL US<br>service@coralbaypoolslv.com</div></div>
  <div class="foot-item" style="left:900px"><div class="badge"><svg viewBox="0 0 44 44" width="44" height="44" fill="none" stroke="#fff" stroke-width="2"><rect x="10" y="10" width="24" height="24" transform="rotate(45 22 22)"/><path d="M22 30s-6-6-6-10a6 6 0 0 1 12 0c0 4-6 10-6 10z"/><circle cx="22" cy="20" r="2"/></svg></div><div>Address line Dummy here<br>Address line Dummy here</div></div>
  <div class="foot-rule" style="top:170px"></div>
  <nav class="foot-nav"><span>ABOUT US</span>|<span>OUR SERVICES</span>|<span>FREE ESTIMATES</span>|<span>BLOG</span>|<span>CONTACT US</span></nav>
  <div class="foot-rule" style="top:244px"></div>
  <div class="copyright">Copyright © 2025 All Rights Reserved By Company name</div>
  <div class="social" style="left:1007px"></div>
  <div class="social" style="left:1039px"></div>
  <div class="social" style="left:1071px"></div>
  <div class="social" style="left:1103px"></div>
</footer>

</body>
</html>
```